Postcard Design

business name: COZY HOUR HELPER. I am a mother of 2 well adjusted, successful teenage boys. I decided to start this company caring for kids who are home sick, unable to go to daycare or school, and when their parent cant stay home with them. I was also a career woman for many years, with no friends available or family nearby to help when i was in an emergency situation for childcare. I know how stressful it can be when a child gets sick suddenly and unexpectedly. I would like to help out those parents in need, that have pressing schedules and a sick child at home that they really want to take care of, but cant due to their work pressures and priorities. I want parents to know that their child is safe and I can help them when in need, at last minute. The design should show the child is safe and well cared for and the parent is at ease, able to accomplish their obligations. I have also founded a nonprofit environmental education program in which I teach children in youth summer camps. I have taught creativity arts combined with science curriculum in kindergarten to 8th grade non-formal teaching for the past 5 years. This is a small community, and many people know me. I will be handing out these postcards to local daycares and people I know.

Industry/Entity Type

Business

```html
<!DOCTYPE html>
<html lang="en">
<head>
<meta charset="utf-8">
<title>Cozy Hour Helper Postcard</title>
<link rel="stylesheet" href="https://fonts.googleapis.com/css2?family=Oswald:wght@500;600;700&family=Arimo:wght@400;700&family=Lato:wght@400;700;900&display=swap">
<style>
  :root{
    --blue:#2f4fa3;
    --blue-light:#3c66bd;
    --orange:#f7941d;
    --orange-light:#fcc15a;
    --pink:#e5197e;
    --green:#8dc63f;
    --badge-green:#a6ce39;
    --yellow:#f9e04b;
    --ink:#231f20;
    --white:#ffffff;
    --page:#dcdcdc;
  }
  *{margin:0;padding:0;box-sizing:border-box}
  html,body{width:806px;height:1200px;overflow:hidden;background:var(--page)}
  .canvas{position:relative;width:806px;height:1200px}
  .card{position:absolute;left:61px;width:686px;height:532px;overflow:hidden;background:var(--white);box-shadow:0 3px 10px rgba(0,0,0,.25)}
  .card--front{top:48px}
  .card--back{top:620px}
  .layer{position:absolute;left:0;top:0;width:686px;height:532px}
  .abs{position:absolute;white-space:nowrap}

  .brand-name{left:25px;top:26px;font:600 31px/1 "Oswald",sans-serif;color:var(--yellow);letter-spacing:.3px}
  .headline{left:24px;top:126px;font:700 68px/1 "Oswald",sans-serif;color:var(--pink);-webkit-text-stroke:2px var(--white);paint-order:stroke fill;text-shadow:0 2px 3px rgba(0,0,0,.25);letter-spacing:1px}
  .subhead{left:25px;top:211px;font:400 28px/1 "Arimo",sans-serif;color:var(--ink)}
  .intro{left:25px;top:258px;width:262px;white-space:normal;font:400 14px/20px "Lato",sans-serif;color:var(--ink);text-align:justify;hyphens:auto;-webkit-hyphens:auto}

  .badge-text{left:419px;top:294px;width:140px;text-align:center;font:700 20px/1.2 "Arimo",sans-serif}
  .badge-text .accent{color:var(--pink);display:block}
  .badge-text .strong{color:var(--ink);font-size:23px;display:block}

  .contact-bar{left:25px;top:485px;display:flex;align-items:baseline;gap:10px;color:var(--white);font-family:"Lato",sans-serif}
  .contact-name{font-size:15px;font-weight:700}
  .call-label{font-size:20px;font-weight:900;color:var(--yellow);margin-left:8px}
  .call-number{font-size:22px;font-weight:700;margin-left:-6px}
  .web{font-size:15px;font-weight:700;display:flex;align-items:center;gap:6px;margin-left:8px}
  .icon{width:11px;height:11px}

  .back-title{left:17px;top:37px;font:600 22px/1 "Oswald",sans-serif;color:var(--white);letter-spacing:.4px}
  .back-sub{left:17px;top:70px;font:400 19px/1 "Arimo",sans-serif;color:var(--ink)}
  .back-tagline{left:17px;top:407px;font:600 17px/1 "Oswald",sans-serif;color:var(--white);letter-spacing:.4px}
  .back-contact{left:25px;top:472px;color:var(--white);font:700 14.5px/1 "Lato",sans-serif;display:flex;align-items:center;gap:8px}
  .back-web{left:25px;top:496px;color:var(--white);font:700 14.5px/1 "Lato",sans-serif;display:flex;align-items:center;gap:6px}
  .stamp-box{position:absolute;left:585px;top:37px;width:61px;height:83px;border:1.5px solid #555}
</style>
</head>
<body>
<div class="canvas">

  <section class="card card--front">
    <svg class="layer" viewBox="0 0 686 532" aria-hidden="true">
      <defs>
        <radialGradient id="sunburst" cx="0.35" cy="0.5" r="0.7">
          <stop offset="0" stop-color="#fcc15a"/>
          <stop offset="1" stop-color="#f7941d"/>
        </radialGradient>
        <linearGradient id="bandBlue" x1="0" y1="0" x2="1" y2="0">
          <stop offset="0" stop-color="#2f4fa3"/>
          <stop offset="1" stop-color="#3c66bd"/>
        </linearGradient>
      </defs>
      <rect width="686" height="532" fill="url(#sunburst)"/>
      <path d="M0,0 H360 V78 Q180,96 0,118 Z" fill="url(#bandBlue)"/>
      <path d="M0,112 Q180,92 340,78" fill="none" stroke="#e5197e" stroke-width="5"/>
      <path d="M0,120 Q180,100 340,86" fill="none" stroke="#8dc63f" stroke-width="5"/>
      <circle cx="582" cy="54" r="297" fill="#8dc63f"/>
      <circle cx="582" cy="54" r="289" fill="#e5197e"/>
      <circle cx="582" cy="54" r="284" fill="#f9e04b"/>
      <circle cx="582" cy="54" r="279" fill="#ffffff"/>
      <path d="M0,446 Q300,420 686,424" fill="none" stroke="#e5197e" stroke-width="5"/>
      <path d="M0,456 Q320,432 686,440" fill="none" stroke="#8dc63f" stroke-width="6"/>
      <path d="M0,462 Q340,440 686,452 V532 H0 Z" fill="url(#bandBlue)"/>
    </svg>
    <svg class="layer" viewBox="0 0 686 532" role="img" aria-label="Photo: three children lying on the floor reading a book together">
      <defs>
        <clipPath id="photoCircle"><circle cx="582" cy="54" r="279"/></clipPath>
        <linearGradient id="readingPhoto" x1="0" y1="0" x2="1" y2="0">
          <stop offset="0" stop-color="#dcecc4"/>
          <stop offset="0.45" stop-color="#f4e6a0"/>
          <stop offset="1" stop-color="#f1c3cf"/>
        </linearGradient>
      </defs>
      <rect x="300" y="0" width="386" height="340" fill="url(#readingPhoto)" opacity="0.6" clip-path="url(#photoCircle)"/>
    </svg>
    <svg class="layer" viewBox="0 0 686 532" aria-hidden="true">
      <g fill="#a6ce39" stroke="#e8f3c8" stroke-width="2">
        <circle cx="551" cy="343" r="20"/><circle cx="543" cy="374" r="20"/>
        <circle cx="520" cy="397" r="20"/><circle cx="489" cy="405" r="20"/>
        <circle cx="458" cy="397" r="20"/><circle cx="435" cy="374" r="20"/>
        <circle cx="427" cy="343" r="20"/><circle cx="435" cy="312" r="20"/>
        <circle cx="458" cy="289" r="20"/><circle cx="489" cy="281" r="20"/>
        <circle cx="520" cy="289" r="20"/><circle cx="543" cy="312" r="20"/>
      </g>
      <circle cx="489" cy="343" r="62" fill="#a6ce39"/>
    </svg>

    <div class="abs brand-name">COZY HOUR HELPER</div>
    <div class="abs headline">GROOM</div>
    <div class="abs subhead">YOUR CHILDEN</div>
    <p class="abs intro">I know how stressful it can be when a child gets sick suddenly and unexpectedly. I would like to help out those parents in need, that have pressing schedules and a sick child at home that they really want to take care of, but cant due to their work pressures and priorities.</p>

    <div class="abs badge-text">
      <span class="accent">5 years of</span>
      <span class="strong">Teaching</span>
      <span class="accent">Experience</span>
    </div>

    <div class="abs contact-bar">
      <span class="contact-name">Dana Whitfield</span>
      <span class="call-label">call now</span>
      <span class="call-number">-(555) 214-7790</span>
      <span class="web">
        <svg class="icon" viewBox="0 0 12 12" aria-hidden="true"><circle cx="6" cy="6" r="5" fill="none" stroke="#f9e04b" stroke-width="1.3"/><path d="M1,6 H11 M6,1 Q2.5,6 6,11 M6,1 Q9.5,6 6,11" fill="none" stroke="#f9e04b" stroke-width="1"/></svg>
        www.cozyhourhelper.net/dana52
      </span>
    </div>
  </section>

  <section class="card card--back">
    <svg class="layer" viewBox="0 0 686 532" aria-hidden="true">
      <defs>
        <radialGradient id="backOrange" cx="0.3" cy="0.4" r="0.8">
          <stop offset="0" stop-color="#fcc15a"/>
          <stop offset="1" stop-color="#f7941d"/>
        </radialGradient>
        <clipPath id="panelShape"><path d="M0,0 H228 Q400,250 300,462 H0 Z"/></clipPath>
      </defs>
      <path d="M244,0 Q416,250 316,462" fill="none" stroke="#8dc63f" stroke-width="6"/>
      <path d="M236,0 Q408,250 308,462" fill="none" stroke="#2f4fa3" stroke-width="7"/>
      <path d="M0,0 H228 Q400,250 300,462 H0 Z" fill="url(#backOrange)"/>
      <g clip-path="url(#panelShape)">
        <rect x="0" y="109" width="400" height="4" fill="#e5197e"/>
        <rect x="0" y="379" width="400" height="4" fill="#e5197e"/>
      </g>
      <path d="M300,448 L318,462 L300,462 Z" fill="#222"/>
      <rect x="0" y="462" width="300" height="70" fill="#2f4fa3"/>
    </svg>
    <svg class="layer" viewBox="0 0 686 532" role="img" aria-label="Photo: five smiling children huddled together under a blue sky">
      <defs>
        <clipPath id="photoPanel"><path d="M0,0 H228 Q400,250 300,462 H0 Z"/></clipPath>
        <linearGradient id="kidsPhoto" x1="0" y1="0" x2="0" y2="1">
          <stop offset="0" stop-color="#7fb9ea"/>
          <stop offset="0.45" stop-color="#b9d8f1"/>
          <stop offset="0.7" stop-color="#e9a07a"/>
          <stop offset="1" stop-color="#5fb7d8"/>
        </linearGradient>
      </defs>
      <rect x="0" y="113" width="400" height="266" fill="url(#kidsPhoto)" clip-path="url(#photoPanel)"/>
    </svg>

    <div class="abs back-title">SAFE AND WELL CARE</div>
    <div class="abs back-sub">FOR YOUR CHILDREN</div>
    <div class="abs back-tagline">MAKE YOUR CHILD FUTER BRIGHT</div>
    <div class="abs back-contact">
      <span>Dana Whitfield</span>
      <svg class="icon" viewBox="0 0 12 12" aria-hidden="true"><path d="M2.5,1 L4.5,1 L5.3,3.6 L4,4.6 Q5,7 7.4,8 L8.4,6.7 L11,7.5 L11,9.5 Q10.5,11 9,11 Q1,10 1,2.5 Q1,1 2.5,1 Z" fill="#f9e04b"/></svg>
      <span style="margin-left:-4px">(555) 214-7790</span>
    </div>
    <div class="abs back-web">
      <svg class="icon" viewBox="0 0 12 12" aria-hidden="true"><circle cx="6" cy="6" r="5" fill="none" stroke="#f9e04b" stroke-width="1.3"/><path d="M1,6 H11 M6,1 Q2.5,6 6,11 M6,1 Q9.5,6 6,11" fill="none" stroke="#f9e04b" stroke-width="1"/></svg>
      www.cozyhourhelper.net/dana52
    </div>
    <div class="stamp-box" aria-hidden="true"></div>
  </section>

</div>
</body>
</html>
```